Business card design needed

I would like a one sided black business card with the information provided above. Refer to my website www.brightvolleyracquets.com.au for an example of colors I have used for my site, would like to keep this consistent for my business cards also, I will upload my logo below.

I am a new small business that provides tennis customers with racquet re stringing, tennis strings and accessories.

Industry/Entity Type

Small Business

Contact Information for Business Card

Bright Volley Tennis

Owen Whitby
Managing Director

brightvolleyracquets@mailbox.example
www.brightvolleyracquets.com.au
0491 726 305

Racquet Restringing/Tennis Strings/Accessories

Requirements
Must have
• Must have my logo and card must be black

```html
<!DOCTYPE html>
<html lang="en">
<head>
<meta charset="utf-8">
<title>Bright Volley Tennis – Business Cards</title>
<link rel="stylesheet" href="https://fonts.googleapis.com/css2?family=Source+Sans+3:wght@400;600&display=swap">
<style>
  :root {
    --backdrop: #9a6238;
    --card-black: #000000;
    --lime: #b5cc2e;
    --white: #ffffff;
    --soft-white: #e8e8e8;
  }
  * { margin: 0; padding: 0; box-sizing: border-box; }
  html, body {
    width: 1200px;
    height: 475px;
    overflow: hidden;
    background: var(--backdrop);
    font-family: "Source Sans 3", "Myriad Pro", Arial, sans-serif;
  }
  .stage {
    position: relative;
    width: 1200px;
    height: 475px;
  }
  .card {
    position: absolute;
    background: var(--card-black);
    box-shadow: 0 2px 6px rgba(0,0,0,0.35);
  }
  .card--front { left: 21px; top: 73px; width: 546px; height: 312px; }
  .card--back  { left: 602px; top: 81px; width: 547px; height: 313px; }

  .brand-name {
    position: absolute;
    color: var(--lime);
    font-weight: 600;
    white-space: nowrap;
    line-height: 1;
  }
  .card--front .brand-name {
    left: 52px;
    top: 72px;
    font-size: 36px;
  }
  .card--back .brand-name {
    left: 0;
    right: 0;
    top: 120px;
    text-align: center;
    font-size: 40px;
  }

  .holder {
    position: absolute;
    left: 54px;
    top: 207px;
  }
  .holder__name {
    color: var(--lime);
    font-size: 19px;
    font-weight: 400;
    text-transform: uppercase;
    letter-spacing: 0.3px;
    line-height: 1.1;
  }
  .holder__title {
    color: var(--lime);
    font-size: 13px;
    line-height: 1.4;
  }

  .contact-list {
    position: absolute;
    left: 208px;
    top: 200px;
    list-style: none;
  }
  .contact-list__item {
    display: flex;
    align-items: center;
    height: 19px;
    color: var(--white);
    font-size: 13.5px;
  }
  .contact-list__icon {
    width: 12px;
    height: 12px;
    margin-right: 11px;
    flex: none;
  }

  .card__url {
    position: absolute;
    left: 0;
    right: 0;
    top: 262px;
    text-align: center;
    color: var(--soft-white);
    font-size: 13px;
    letter-spacing: 2.2px;
  }
</style>
</head>
<body>
<main class="stage">

  <section class="card card--front" aria-label="Business card front">
    <div class="brand-name">Bright Volley Tennis</div>

    <div class="holder">
      <p class="holder__name">Owen Whitby</p>
      <p class="holder__title">Managing Director</p>
    </div>

    <ul class="contact-list">
      <li class="contact-list__item">
        <svg class="contact-list__icon" viewBox="0 0 12 12" aria-hidden="true">
          <path d="M2.5 1 L4.5 1 L5 3.5 L3.8 4.4 Q4.8 6.8 7.6 8.2 L8.5 7 L11 7.5 L11 9.5 Q10.5 11 9 11 Q1 10 1 2.5 Q1 1 2.5 1 Z" fill="var(--lime)"/>
        </svg>
        0491 726 305
      </li>
      <li class="contact-list__item">
        <svg class="contact-list__icon" viewBox="0 0 12 12" aria-hidden="true">
          <rect x="1" y="3" width="10" height="7" fill="var(--lime)"/>
          <path d="M1 3 L6 7 L11 3" fill="none" stroke="var(--card-black)" stroke-width="1"/>
        </svg>
        brightvolleyracquets@mailbox.example
      </li>
      <li class="contact-list__item">
        <svg class="contact-list__icon" viewBox="0 0 12 12" aria-hidden="true">
          <circle cx="6" cy="6" r="5" fill="none" stroke="var(--lime)" stroke-width="1.2"/>
          <ellipse cx="6" cy="6" rx="2.2" ry="5" fill="none" stroke="var(--lime)" stroke-width="1"/>
          <line x1="1" y1="6" x2="11" y2="6" stroke="var(--lime)" stroke-width="1"/>
        </svg>
        www.brightvolleyracquets.com.au
      </li>
    </ul>
  </section>

  <section class="card card--back" aria-label="Business card back">
    <div class="brand-name">Bright Volley Tennis</div>
    <p class="card__url">www.brightvolleyracquets.com.au</p>
  </section>

</main>
</body>
</html>
```